Animal Eye Clinic needs a Business card

We are a new veterinary ophthalmology practice (Ridgeline Pet Vision Care) and we need a business card designed. We only see animal eyes - we are not a regular veterinary clinic. We already have a logo. We are looking for a professional, good looking business card to hand out to our clients. We are looking for something simple but professional and contemporary. Our logo is likely the only picture/graphic that needs to be on the card.
Updates

Contact Information for Business Card

Delia Vossman, BSc, DVM, MSc, DipACVO
Veterinary Ophthalmologist

Phone: 250.418.3927
Email: ridgelinepetvisioncare@mailbox-example.net
Website: ridgelinepetvisioncare-example.net
Address: 1874 Thornbury Rd
Kelowna, BC, V1X 4M9

Colors

Designer to choose colors to be used in the design.

Requirements
Must have
• Our logo (attached)

```html
<!DOCTYPE html>
<html lang="en">
<head>
<meta charset="utf-8">
<title>Ridgeline Pet Vision Care – Business Card</title>
<link href="https://fonts.googleapis.com/css2?family=Roboto:wght@400;500;700&display=swap" rel="stylesheet">
<style>
  :root {
    --backdrop: #3a302b;
    --card: #2c2c2e;
    --edge: #1b9aa9;
    --teal: #1b9aa9;
    --text: #e6e6e6;
    --rule: #8a8a8a;
  }
  * { box-sizing: border-box; margin: 0; padding: 0; }
  html, body { width: 1200px; height: 805px; overflow: hidden; }
  body {
    background: var(--backdrop);
    font-family: "Roboto", Arial, sans-serif;
    position: relative;
  }
  .card {
    position: absolute;
    width: 540px;
    height: 309px;
    background: var(--card);
    border: 2px solid var(--edge);
    box-shadow: 0 12px 30px rgba(0,0,0,.45);
  }
  .card--front { left: 40px; top: 150px; }
  .card--back { left: 620px; top: 346px; }

  .brand {
    display: flex;
    align-items: center;
    gap: 12px;
    color: var(--teal);
    font-weight: 700;
  }
  .brand__dot {
    flex: none;
    border-radius: 50%;
    background: var(--teal);
  }
  .card--front .brand {
    position: absolute;
    left: 50%; top: 50%;
    transform: translate(-50%, -50%);
    font-size: 28px;
    white-space: nowrap;
  }
  .card--front .brand__dot { width: 42px; height: 42px; }

  .card--back .brand {
    position: absolute;
    left: 32px; top: 118px;
    width: 190px;
    font-size: 17px;
    line-height: 1.15;
    gap: 9px;
  }
  .card--back .brand__dot { width: 26px; height: 26px; }

  .divider {
    position: absolute;
    left: 236px; top: 92px;
    width: 1px; height: 132px;
    background: var(--rule);
  }
  .contact {
    position: absolute;
    left: 252px; top: 88px;
    width: 280px;
    color: var(--text);
    font-size: 12px;
    line-height: 1.45;
  }
  .contact__name { color: var(--teal); font-weight: 700; font-size: 14px; }
  .contact__creds { font-size: 8.5px; font-weight: 500; }
  .contact__title { margin-bottom: 6px; }
  .contact__address { margin-bottom: 6px; }
  .contact__line { display: flex; align-items: center; gap: 6px; white-space: nowrap; font-size: 11.5px; }
  .contact__line svg { flex: none; width: 10px; height: 10px; fill: var(--teal); }
  .contact__domain { color: var(--teal); }
</style>
</head>
<body>
  <section class="card card--front">
    <div class="brand"><span class="brand__dot"></span><span class="brand__name">Ridgeline Pet Vision Care</span></div>
  </section>

  <section class="card card--back">
    <div class="brand"><span class="brand__dot"></span><span class="brand__name">Ridgeline Pet Vision Care</span></div>
    <div class="divider"></div>
    <div class="contact">
      <p class="contact__name">Delia Vossman, <span class="contact__creds">BSc, DVM, MSc, DipACVO</span></p>
      <p class="contact__title">Veterinary Ophthalmologist</p>
      <p class="contact__address">1874 Thornbury Rd<br>Kelowna, BC, V1X 4M9</p>
      <p class="contact__line">
        <svg viewBox="0 0 10 10" aria-hidden="true"><path d="M2 0.5l1.6 2.2-1 1a5 5 0 0 0 3.7 3.7l1-1L9.5 8 8.3 9.5C4 9.5 0.5 6 0.5 1.7z"/></svg>
        250.418.3927
      </p>
      <p class="contact__line">
        <svg viewBox="0 0 10 10" aria-hidden="true"><path d="M0 2h10v6H0z M0.6 2.3L5 5.6 9.4 2.3" stroke="#2c2c2e" stroke-width=".8"/></svg>
        ridgelinepetvisioncare@mailbox-example.net
      </p>
      <p class="contact__line">
        <svg viewBox="0 0 10 10" aria-hidden="true"><circle cx="5" cy="5" r="4.6"/><path d="M0.5 5h9M5 0.5c-2.4 2.6-2.4 6.4 0 9M5 0.5c2.4 2.6 2.4 6.4 0 9" stroke="#2c2c2e" stroke-width=".7" fill="none"/></svg>
        www.<span class="contact__domain">ridgelinepetvisioncare-example.net</span>
      </p>
    </div>
  </section>
</body>
</html>
```